Harborline Business Card Designs***

WE ARE A FULL SERVICE FACILITY. ALL KINDS OF CAR/ TRK, REPAIR. CUSTOM WHEELS & TIRES. BRAKES, MUFFLERS, SHOCK, STRUTS...BATTERIES, STARTERS, ATERNATORS, TUNE UPS (WE DO IT ALL) ESTABLISHED IN 2004, LOCALLY OWNED AND OPERATED.... I AM OPEN TO SUGGESTIONS AS WELL ON ANY IDEAS

Contact Information for Business Card

WE DO COMPLETE AUTO REPAIR AND WHEELS, TIRES AND ACCESSORIES AT OUR STORE. I NAME OF SHOP (HARBORLINE AUTOMOTIVE GROUP) WOULD LIKE OUR EMAIL ON IT (HARBORLINEAUTOGROUP@QUVIX.NET) PHONE NUMBER 567-302-GEAR (4327) BUSINESS HOURS MON- FRI 7:30-5 SNAPGRID LOGO WITH (@HARBORLINE_AUTO_WESTRIDGE) WEBSITE (KESTRELROADWORKS.NET)FRIENDLOOP LOGO W/ (FRIENDLOOP.NET/HARBORLINEAUTOMOTIVE) AN A+/ QCR LOGO (THE LITTLE TORCH)... MAYBE EVEN EST.2004 INSIDE OF A "POW SIGN" (UNLESS IT GETS TO CLUTTERED) AND ON THE BACK OF THE CARD MAYBE A FAINT PICTURE OF "SOMETHING" IN BACKGROUND BUT STILL BE ABLE TO SEE THE ESTIMATE WE WRITE ON THE BACK. I WOULD LIKE ON THE BACK, DOWN IN THE RIGHT HAND CORNER A SPOT FOR A DATE AND INT. WE ALSO EXCEPT: Orba, TRUSTPLATE, KELMORE AND ZINCWAY

```html
<!DOCTYPE html>
<html lang="en">
<head>
<meta charset="utf-8">
<title>Harborline Automotive Group — Business Card</title>
<link rel="stylesheet" href="https://fonts.googleapis.com/css2?family=Michroma&family=Roboto+Condensed:wght@400;700&display=swap">
<style>
  :root {
    --page: #e9e7e3;
    --card: #eeeeee;
    --ink: #111111;
    --text: #222222;
    --brand: #1d58b5;
    --hours: #3a3e9e;
    --burst: #17b4ea;
    --rule: #3a3a3a;
    --muted: #bdbdbd;
  }
  * { box-sizing: border-box; margin: 0; padding: 0; }
  html, body { width: 1200px; height: 1200px; overflow: hidden; }
  body {
    background: var(--page);
    font-family: "Roboto Condensed", sans-serif;
    color: var(--text);
    position: relative;
  }
  .card {
    position: absolute;
    left: 150px;
    width: 900px;
    height: 540px;
    background: var(--card);
    overflow: hidden;
    box-shadow: 0 6px 18px rgba(0,0,0,.18);
  }
  .card--front { top: 40px; }
  .card--back { top: 620px; }
  .card__backdrop { position: absolute; inset: 0; }
  .card--front .card__backdrop {
    background: radial-gradient(ellipse at 48% 30%, #dcdcdc 0%, #e4e2e2 40%, #ebeaea 75%, #efefef 100%);
  }
  .card--back .card__backdrop {
    background:
      linear-gradient(180deg, rgba(255,255,255,0) 0%, rgba(255,255,255,.55) 42%, rgba(255,255,255,.2) 58%, rgba(255,255,255,0) 100%),
      radial-gradient(circle at 14% 18%, #dcdcdc 0 18%, transparent 19%),
      radial-gradient(circle at 38% 18%, #dcdcdc 0 18%, transparent 19%),
      radial-gradient(circle at 64% 18%, #dcdcdc 0 18%, transparent 19%),
      radial-gradient(circle at 89% 18%, #e3d3d3 0 18%, transparent 19%),
      radial-gradient(circle at 14% 58%, #dedede 0 18%, transparent 19%),
      radial-gradient(circle at 38% 58%, #dedede 0 18%, transparent 19%),
      radial-gradient(circle at 64% 58%, #dcdcd6 0 18%, transparent 19%),
      radial-gradient(circle at 89% 58%, #dedede 0 18%, transparent 19%),
      #ececec;
  }
  .brand-name {
    position: absolute;
    font-weight: 700;
    font-size: 70px;
    line-height: 1;
    color: var(--brand);
    letter-spacing: -1px;
    white-space: nowrap;
  }
  .brand-tagline {
    position: absolute;
    font-family: "Michroma", sans-serif;
    color: var(--ink);
    white-space: nowrap;
    line-height: 1;
  }
  .card--front .brand-name { top: 158px; left: 0; right: 0; text-align: center; }
  .card--front .brand-tagline {
    left: 0; right: 0; text-align: center;
    top: 250px; font-size: 34px; letter-spacing: 1px;
  }
  .hours {
    position: absolute; left: 0; right: 0; top: 292px;
    text-align: center; font-size: 26px; color: var(--hours);
  }
  .rule {
    position: absolute; height: 3px;
    background: linear-gradient(90deg, transparent, var(--rule) 15%, var(--rule) 85%, transparent);
  }
  .card--front .rule { left: 36px; right: 8px; top: 352px; }
  .contact-row {
    position: absolute; left: 0; right: 0;
    display: flex; justify-content: center; align-items: center;
  }
  .contact-row--primary { top: 384px; }
  .contact-row--social { top: 444px; }
  .contact {
    display: flex; align-items: center; gap: 8px;
    font-size: 19px; color: var(--text);
    padding: 0 12px; height: 54px;
  }
  .contact + .contact { border-left: 1.5px solid #777; }
  .contact svg { flex: none; }
  .contact__mark { width: 22px; height: 22px; flex: none; }
  .contact__mark--snapgrid { background: #6b4a3a; border-radius: 4px; }
  .contact__mark--friendloop { background: #4a6fb0; border-radius: 4px; }
  .listing-badge { width: 36px; height: 44px; background: #7fa2b8; border-radius: 4px; }
  .card--back .brand-name { top: 160px; left: 254px; }
  .card--back .brand-tagline { left: 192px; top: 252px; font-size: 26px; letter-spacing: 1px; }
  .est-burst { position: absolute; left: 615px; top: 218px; }
  .card--back .rule { left: 40px; right: 10px; top: 390px; }
  .payments {
    position: absolute; left: 100px; top: 422px;
    display: flex; align-items: center; gap: 8px;
  }
  .payment {
    display: flex; align-items: center; gap: 5px;
    font-size: 16px; font-weight: 700; color: var(--text);
    background: #ffffff; border: 1px solid #cfcfcf;
    padding: 0 7px; height: 48px;
  }
  .payment__dot { width: 12px; height: 12px; border-radius: 50%; background: #d6a21e; }
  .payment__square { width: 11px; height: 11px; background: var(--brand); }
  .estimate-fields {
    position: absolute; left: 636px; top: 424px;
    font-size: 20px; line-height: 26px; color: var(--ink);
  }
  .estimate-fields .placeholder { color: var(--muted); }
</style>
</head>
<body>

<section class="card card--front" aria-label="Card front">
  <div class="card__backdrop" role="img" aria-label="Faint photo of a chrome engine bay with air cleaner"></div>
  <div class="brand-name">Harborline</div>
  <div class="brand-tagline">AUTOMOTIVE GROUP</div>
  <div class="hours">BUSINESS HOURS MON- FRI 7:30-5</div>
  <div class="rule"></div>

  <div class="contact-row contact-row--primary">
    <div class="contact">
      <svg width="30" height="30" viewBox="0 0 24 24" aria-hidden="true"><path fill="#222" d="M6.6 10.8c1.4 2.8 3.8 5.1 6.6 6.6l2.2-2.2c.3-.3.7-.4 1-.2 1.1.4 2.3.6 3.6.6.6 0 1 .4 1 1V20c0 .6-.4 1-1 1C10.6 21 3 13.4 3 4c0-.6.4-1 1-1h3.5c.6 0 1 .4 1 1 0 1.3.2 2.5.6 3.6.1.3 0 .7-.2 1z"/></svg>
      <span>567-302-Gear (4327)</span>
    </div>
    <div class="contact">
      <svg width="40" height="40" viewBox="0 0 40 40" aria-hidden="true"><circle cx="20" cy="20" r="18" fill="#333"/><text x="20" y="25" text-anchor="middle" font-family="Roboto Condensed, sans-serif" font-size="14" font-weight="700" fill="#fff">www</text></svg>
      <span>kestrelroadworks.net</span>
    </div>
    <div class="contact">
      <svg width="40" height="28" viewBox="0 0 40 28" aria-hidden="true"><rect x="1" y="1" width="38" height="26" fill="#fff" stroke="#222" stroke-width="2"/><path d="M1 1 L20 16 L39 1" fill="none" stroke="#222" stroke-width="2"/><path d="M1 27 L15 12 M39 27 L25 12" stroke="#222" stroke-width="2"/></svg>
      <span>harborlineautogroup@quvix.net</span>
    </div>
  </div>

  <div class="contact-row contact-row--social">
    <div class="contact"><span class="contact__mark contact__mark--snapgrid"></span><span>harborline_auto_westridge</span></div>
    <div class="contact"><span class="contact__mark contact__mark--friendloop"></span><span>harborlineautomotive</span></div>
    <div class="contact"><span class="listing-badge" role="img" aria-label="Accreditation listing badge"></span></div>
  </div>
</section>

<section class="card card--back" aria-label="Card back">
  <div class="card__backdrop" role="img" aria-label="Faint photo grid of custom alloy wheels"></div>
  <div class="brand-name">Harborline</div>
  <div class="brand-tagline">AUTOMOTIVE GROUP</div>
  <svg class="est-burst" width="186" height="86" viewBox="0 0 196 90" aria-label="Established 2004">
    <polygon fill="var(--burst)" points="4,44 34,30 26,8 66,20 98,2 122,18 158,8 156,30 192,44 160,56 170,84 128,70 98,88 70,72 30,82 38,58"/>
    <text x="98" y="55" text-anchor="middle" font-family="Roboto Condensed, sans-serif" font-size="28" fill="#fff">EST.2004</text>
  </svg>
  <div class="rule"></div>

  <div class="payments">
    <div class="payment"><span class="payment__dot"></span>Zincway</div>
    <div class="payment"><span class="payment__square"></span>Trustplate</div>
    <div class="payment">Orba</div>
    <div class="payment">Kelmore</div>
  </div>

  <div class="estimate-fields">
    <div>DATE : <span class="placeholder">DD/MM/YYYY</span></div>
    <div>INT :</div>
  </div>
</section>

</body>
</html>
```